Upscale business cards needed for Board of Directors

We need professional business cards created for members of our family business Board of Directors. We would like these relatively simple and straightforward, but also with a unique element to set them apart. Probably stick with neutral and simple colors - white, grey etc. We need space for the traditional elements, including name, title, address, email/phone number. And we will be creating several from this template so it needs to be template that is easy to switch information in and out of.
Business
See description

```html
<!DOCTYPE html>
<html lang="en">
<head>
<meta charset="utf-8">
<title>Harborline Holdings – Business Cards</title>
<link href="https://fonts.googleapis.com/css2?family=Lato:wght@400;900&display=swap" rel="stylesheet">
<style>
  :root {
    --backdrop: #d9d9d7;
    --paper: #ffffff;
    --ink: #111111;
    --panel: #000000;
    --gold: #b3a27c;
    --muted: #444444;
  }
  * { margin: 0; padding: 0; box-sizing: border-box; }
  html, body {
    width: 1200px; height: 900px; overflow: hidden;
    background: var(--backdrop);
    font-family: 'Lato', sans-serif;
  }
  .canvas { position: relative; width: 1200px; height: 900px; }
  .card {
    position: absolute;
    width: 580px; height: 330px;
    background: var(--paper);
    box-shadow: 0 6px 18px rgba(0,0,0,0.18);
    overflow: hidden;
  }
  .card--front { left: 520px; top: 80px; }
  .card--back { left: 100px; top: 480px; display: flex; }

  .wordmark { text-align: center; text-transform: uppercase; font-weight: 900; line-height: 1; }
  .wordmark__name { display: block; font-size: 50px; letter-spacing: 1px; }
  .wordmark__sub { display: block; font-size: 22px; letter-spacing: 12px; margin-top: 8px; padding-left: 12px; }

  .card--front .wordmark { color: var(--ink); margin-top: 100px; }
  .card--front .site {
    position: absolute; left: 0; right: 0; bottom: 48px;
    text-align: center; font-size: 15px; letter-spacing: 2px; color: var(--ink);
  }

  .back__panel {
    width: 230px; height: 100%;
    background: var(--panel);
    display: flex; align-items: center; justify-content: center;
  }
  .back__panel .wordmark { color: var(--paper); }
  .back__panel .wordmark__name { font-size: 34px; }
  .back__panel .wordmark__sub { font-size: 15px; letter-spacing: 8px; margin-top: 6px; padding-left: 8px; }
  .back__rule { width: 3px; height: 100%; background: var(--gold); margin-left: 14px; }

  .contact { padding: 70px 0 0 50px; color: var(--ink); }
  .contact__name { font-size: 24px; font-weight: 400; }
  .contact__title { font-size: 16px; color: var(--gold); margin-top: 2px; }
  .contact__address { font-size: 16px; line-height: 1.25; margin-top: 12px; }
  .contact__list { list-style: none; margin-top: 8px; }
  .contact__list li { display: flex; align-items: center; font-size: 16px; line-height: 1.4; }
  .contact__list svg { width: 14px; height: 14px; margin-right: 12px; fill: var(--gold); }
</style>
</head>
<body>
<main class="canvas">
  <section class="card card--front" aria-label="Card front">
    <div class="wordmark">
      <span class="wordmark__name">Harborline</span>
      <span class="wordmark__sub">Holdings</span>
    </div>
    <p class="site">www.harborline.com</p>
  </section>

  <section class="card card--back" aria-label="Card back">
    <div class="back__panel">
      <div class="wordmark">
        <span class="wordmark__name">Harborline</span>
        <span class="wordmark__sub">Holdings</span>
      </div>
    </div>
    <div class="back__rule"></div>
    <div class="contact">
      <p class="contact__name">Martin Hale</p>
      <p class="contact__title">Director</p>
      <p class="contact__address">4100 Elm Row<br>Dalton TX 75000</p>
      <ul class="contact__list">
        <li><svg viewBox="0 0 16 16" aria-hidden="true"><path d="M3 1l3 3-1.5 2a9 9 0 0 0 5.5 5.5L12 10l3 3-2 2C6 15 1 10 1 3z"/></svg>555 014 2200</li>
        <li><svg viewBox="0 0 16 16" aria-hidden="true"><rect x="4" y="1" width="8" height="4"/><rect x="1" y="6" width="14" height="6" rx="1"/><rect x="4" y="10" width="8" height="5"/></svg>555 014 2201</li>
        <li><svg viewBox="0 0 16 16" aria-hidden="true"><path d="M1 3h14v10H1z M1 3l7 6 7-6" stroke="#fff" stroke-width="1"/></svg>info@harborline.com</li>
        <li><svg viewBox="0 0 16 16" aria-hidden="true"><circle cx="8" cy="8" r="7"/><path d="M1 8h14M8 1v14M3 4h10M3 12h10" stroke="#fff" stroke-width="0.8" fill="none"/></svg>www.harborline.com</li>
      </ul>
    </div>
  </section>
</main>
</body>
</html>
```